Tandem Hearth Works Pty Ltd

We need business cards for a company based in Perth, we install, service and maintain fire equipment.
On the front we want a great design with our logo and a small spot for our full company name, general company email address and office number. On the back we need space for our name, title, mobile number and email address on the back.

Target Market(s)

Facility managers and commercial/industrial building owners/occupiers.

Contact Information for Business Card

Font styles to use
Sans Serif

Requirements
Must have
• Please only submit 5 of your best samples.
Darker tones are preferred.
Nice to have
• We want to use, black, red and grey. Keep it modern and clean.
I've attached the company logo and a sample of a boarder we use on our emergency plans.
Should not have
• No preference. Let the designer choose.

```html
<!DOCTYPE html>
<html lang="en">
<head>
<meta charset="utf-8">
<title>Tandem Hearth Works Pty Ltd – Business Cards</title>
<link rel="stylesheet" href="https://fonts.googleapis.com/css2?family=Arimo:wght@400;700&display=swap">
<style>
  :root {
    --backdrop: #b8b8b8;
    --brand-red: #ed1c24;
    --brand-red-deep: #d91a24;
    --paper: #ffffff;
    --ink: #2a2a2a;
    --font-main: "Arimo", Arial, sans-serif;
  }
  * { box-sizing: border-box; margin: 0; padding: 0; }
  html, body {
    width: 1200px; height: 801px; overflow: hidden;
    background: var(--backdrop);
    font-family: var(--font-main);
  }
  .card {
    position: absolute; top: 274px;
    width: 443px; height: 263px; overflow: hidden;
  }

  /* Person side */
  .card--person { left: 153px; background: var(--paper); }
  .side-band {
    position: absolute; left: 0; top: 0; bottom: 0;
    width: 44px; background: var(--brand-red);
  }
  .side-rule {
    position: absolute; left: 48px; top: 0; bottom: 0;
    width: 5px; background: var(--brand-red);
  }
  .brand-name {
    position: absolute; left: 252px; top: 50px;
    font-size: 70px; font-weight: 700; line-height: 1;
    color: var(--brand-red); letter-spacing: -1px;
  }
  .person { position: absolute; left: 70px; top: 155px; }
  .person__name {
    font-size: 18px; font-weight: 700; color: var(--brand-red);
    line-height: 1.05; letter-spacing: 0.2px;
  }
  .person__title { font-size: 14px; color: var(--ink); line-height: 1.2; }
  .person__contacts { margin-top: 15px; list-style: none; }
  .person__contacts li {
    display: flex; align-items: center; gap: 6px;
    font-size: 14px; color: var(--ink); line-height: 18px;
  }
  .icon { width: 13px; height: 13px; flex: none; }

  /* Company side */
  .card--company { left: 625px; background: var(--brand-red); color: var(--paper); }
  .brand-watermark {
    position: absolute; left: -8px; top: 30px;
    font-size: 230px; font-weight: 700; line-height: 1;
    color: var(--brand-red-deep); letter-spacing: -6px;
    white-space: nowrap;
  }
  .company {
    position: absolute; left: 0; right: 0; top: 70px;
    text-align: center;
  }
  .company__name {
    font-size: 20px; font-weight: 700; line-height: 25px; letter-spacing: 0.2px;
  }
  .company__phone {
    margin-top: 12px; font-size: 23px; font-weight: 700; line-height: 1;
  }
  .company__links {
    margin-top: 14px; display: flex; justify-content: center; gap: 16px;
    list-style: none; font-size: 15px;
  }
  .company__links li { display: flex; align-items: center; gap: 5px; }
</style>
</head>
<body>

<section class="card card--person" aria-label="Business card, personal side">
  <div class="side-band"></div>
  <div class="side-rule"></div>
  <div class="brand-name">THW</div>
  <div class="person">
    <h1 class="person__name">MARCUS ELLERY</h1>
    <p class="person__title">Managing Director</p>
    <ul class="person__contacts">
      <li>
        <svg class="icon" viewBox="0 0 14 14" aria-hidden="true">
          <rect x="3" y="0.8" width="8" height="12.4" rx="1.5" fill="none" stroke="#ed1c24" stroke-width="1.5"/>
          <circle cx="7" cy="11" r="0.9" fill="#ed1c24"/>
        </svg>
        555.0142.0142
      </li>
      <li>
        <svg class="icon" viewBox="0 0 14 14" aria-hidden="true">
          <rect x="0.5" y="3" width="13" height="9" fill="#ed1c24"/>
          <path d="M0.5 3 L7 8 L13.5 3" fill="none" stroke="#fff" stroke-width="1"/>
        </svg>
        name@tandemhw.com
      </li>
    </ul>
  </div>
</section>

<section class="card card--company" aria-label="Business card, company side">
  <div class="brand-watermark" aria-hidden="true">THW</div>
  <div class="company">
    <h2 class="company__name">TANDEM HEARTH<br>WORKS PTY LTD</h2>
    <p class="company__phone">555.0190.0190</p>
    <ul class="company__links">
      <li>
        <svg class="icon" viewBox="0 0 14 14" aria-hidden="true">
          <rect x="0.5" y="3" width="13" height="9" fill="#fff"/>
          <path d="M0.5 3 L7 8 L13.5 3" fill="none" stroke="#ed1c24" stroke-width="1"/>
        </svg>
        info@tandemhw.com
      </li>
      <li>
        <svg class="icon" viewBox="0 0 14 14" aria-hidden="true">
          <g fill="none" stroke="#fff" stroke-width="1.1">
            <circle cx="7" cy="7" r="6"/>
            <ellipse cx="7" cy="7" rx="2.6" ry="6"/>
            <path d="M1 7 H13 M2 4 H12 M2 10 H12"/>
          </g>
        </svg>
        www.tandemhw.com
      </li>
    </ul>
  </div>
</section>

</body>
</html>
```